GlassHaven Artbook for Okanagan Region, British Columbia

Creating an art book: GlassHaven, for the Okanagan Wine Region in British Columbia, Canada. Would like smart, modern, clean and linear...cool, sexy urban, not ugly boring suburban... I need a cover that appeals to the wino in all of us! Title: GlassHaven -Marla Dovicki
Updates
Thank you all kindly for your efforts. I have added some files so that you can get a sense of my aesthetic...it's never easy trying to figure it out, is it? I will hopefully have dimensions of book soon...cheers, Marla
would anyone please design a giant wine bottle with the wine label that looks like a label but says glasshaven...just curious to see if it works as a design or not...thank you.
Target Market(s)
Designing this wine art book of quotes to wineries in Okanagan BC. Buyer is wine lover and tourist ready to spend his vacation bucks on this wonderful book!
Look and feel

```html
<!DOCTYPE html>
<html lang="en">
<head>
<meta charset="utf-8">
<title>GlassHaven — Book Cover</title>
<link rel="stylesheet" href="https://fonts.googleapis.com/css2?family=Open+Sans:wght@600&family=Lato:wght@400&display=swap">
<style>
  :root {
    --page-bg: #ffffff;
    --cover-bg: #e4e4e3;
    --bottle-area: #000000;
    --title-red: #e31e24;
    --author-grey: #4a4a4a;
  }
  html, body {
    margin: 0;
    padding: 0;
    width: 1200px;
    height: 1000px;
    overflow: hidden;
    background: var(--page-bg);
  }
  .canvas {
    position: relative;
    width: 1200px;
    height: 1000px;
  }
  .book-cover {
    position: absolute;
    left: 365px;
    top: 156px;
    width: 471px;
    height: 653px;
    background: var(--cover-bg);
    overflow: hidden;
  }
  .bottle-area {
    position: absolute;
    background: var(--bottle-area);
  }
  .bottle-area--horizontal {
    left: 0;
    top: 247px;
    width: 383px;
    height: 118px;
  }
  .bottle-area--tilted {
    left: 191px;
    top: 514px;
    width: 380px;
    height: 120px;
    transform-origin: 0 50%;
    transform: rotate(-31.4deg);
  }
  .cover-title {
    position: absolute;
    left: 25px;
    top: 287px;
    margin: 0;
    font-family: "Open Sans", sans-serif;
    font-weight: 600;
    font-size: 29px;
    line-height: 38px;
    letter-spacing: 3.5px;
    color: var(--title-red);
    text-transform: uppercase;
  }
  .cover-author {
    position: absolute;
    right: 26px;
    top: 579px;
    margin: 0;
    font-family: "Lato", sans-serif;
    font-weight: 400;
    font-size: 13px;
    line-height: 16px;
    letter-spacing: 3px;
    color: var(--author-grey);
    text-transform: uppercase;
  }
</style>
</head>
<body>
<div class="canvas">
  <section class="book-cover">
    <div class="bottle-area bottle-area--horizontal" role="img" aria-label="Black wine bottle silhouette lying horizontally"></div>
    <div class="bottle-area bottle-area--tilted" role="img" aria-label="Black wine bottle silhouette tilted toward the lower left"></div>
    <h1 class="cover-title">GlassHaven</h1>
    <p class="cover-author">Marla Dovicki</p>
  </section>
</div>
</body>
</html>
```